TA BRAMLEY BUSINESS CARD DESIGN PROJECT

We need to utilize our logo that was expertly created on PixelHarbor and now need to match this with a business card design.

```html
<!DOCTYPE html>
<html lang="en">
<head>
<meta charset="UTF-8">
<title>TA BRAMLEY Business Card</title>
<link href="https://fonts.googleapis.com/css2?family=Montserrat:wght@400;500;700&display=swap" rel="stylesheet">
<style>
  :root {
    --page-bg: #1d1d1f;
    --card-bg: #151516;
    --brand-blue: #1059b3;
    --text-light: #f2f2f2;
    --emboss: #262628;
    --wave-line: #0d0d0e;
  }
  * { margin: 0; padding: 0; box-sizing: border-box; }
  html, body {
    width: 1200px; height: 900px; overflow: hidden;
    background: var(--page-bg);
    font-family: 'Montserrat', sans-serif;
  }
  .stage {
    position: relative; width: 1200px; height: 900px;
  }
  .card {
    position: absolute; width: 620px; height: 354px;
    border-radius: 22px; overflow: hidden;
    background: var(--card-bg);
  }
  .card--front { left: 290px; top: 70px; }
  .card--back  { left: 290px; top: 476px; border-bottom: 6px solid var(--brand-blue); }

  .front-wave { position: absolute; inset: 0; }

  .brand-name {
    position: absolute; left: 40px; top: 128px; width: 200px;
    color: var(--brand-blue); font-weight: 700; font-size: 30px;
    letter-spacing: 4px; line-height: 1.15; text-align: center;
  }
  .divider {
    position: absolute; left: 272px; top: 60px; width: 2px; height: 160px;
    background: var(--brand-blue);
  }
  .contact {
    position: absolute; left: 300px; top: 58px; color: var(--text-light);
  }
  .contact__name {
    color: var(--brand-blue); font-weight: 700; font-size: 19px; letter-spacing: 0.5px;
  }
  .contact__title { font-size: 13px; margin-top: 2px; }
  .contact__list { list-style: none; margin-top: 14px; }
  .contact__list li {
    display: flex; align-items: center; gap: 8px;
    font-size: 13px; line-height: 21px;
  }
  .contact__list svg { width: 12px; height: 12px; fill: var(--brand-blue); flex: none; }
  .contact__address { font-size: 13px; line-height: 19px; margin-top: 14px; }

  .back-name {
    position: absolute; inset: 0; display: flex; align-items: center; justify-content: center;
    color: var(--emboss); font-weight: 700; font-size: 58px; letter-spacing: 10px;
  }
</style>
</head>
<body>
<main class="stage">
  <section class="card card--front">
    <svg class="front-wave" viewBox="0 0 620 354" aria-hidden="true">
      <path d="M30 354 C200 300 460 265 620 178 L620 354 Z" fill="var(--brand-blue)"/>
      <path d="M55 344 C230 288 470 250 620 188" fill="none" stroke="var(--wave-line)" stroke-width="2"/>
    </svg>
    <div class="brand-name">TA<br>BRAMLEY</div>
    <div class="divider"></div>
    <div class="contact">
      <div class="contact__name">MARCUS HALE</div>
      <div class="contact__title">Managing Director</div>
      <ul class="contact__list">
        <li><svg viewBox="0 0 12 12"><path d="M2 1h3l1 3-1.5 1a6 6 0 0 0 2.5 2.5L8 6l3 1v3a1 1 0 0 1-1 1A9 9 0 0 1 1 2a1 1 0 0 1 1-1z"/></svg>123 456 789</li>
        <li><svg viewBox="0 0 12 12"><path d="M3 1h6v3H3zM1 5h10v5H9v1H3v-1H1zM4 8v2h4V8z"/></svg>123 456 789</li>
        <li><svg viewBox="0 0 12 12"><path d="M1 3h10v6H1zM1 3l5 3.5L11 3" /></svg>info@yourmail.com</li>
        <li><svg viewBox="0 0 12 12"><circle cx="6" cy="6" r="5"/></svg>www.yourwebsite.com</li>
      </ul>
      <div class="contact__address">Your address, City<br>State, Zip 1234</div>
    </div>
  </section>

  <section class="card card--back">
    <div class="back-name">TA BRAMLEY</div>
  </section>
</main>
</body>
</html>
```